holloway paving service

Needs to have phone number 0418259730 and email markholloway@brightmail.com.au.
ABN 62318470915
name mark holloway

For all your concreting solutions
Excavation
Exposed & colour concrete
House & shed slabs
Driveways
Landing & steps

Contact Information for Business Card

ph 0418259730
email markholloway@brightmail.com.au.
ABN 62318470915
name mark holloway

```html
<!DOCTYPE html>
<html lang="en">
<head>
<meta charset="utf-8">
<title>Holloway Paving Service – Business Card</title>
<link rel="stylesheet" href="https://fonts.googleapis.com/css2?family=Quicksand:wght@500;600;700&display=swap">
<style>
  :root {
    --orange: #e8652a;
    --orange-light: #f27d45;
    --orange-deep: #dc5c22;
    --card-white: #f1f1f1;
    --card-grey: #dedede;
    --backdrop: #ececec;
    --white: #ffffff;
  }
  * { box-sizing: border-box; margin: 0; padding: 0; }
  html, body {
    width: 1200px; height: 960px; overflow: hidden;
    background: var(--backdrop);
    font-family: "Quicksand", "Helvetica Neue", Arial, sans-serif;
  }
  .canvas { position: relative; width: 1200px; height: 960px; }

  .card {
    position: absolute; width: 600px; height: 342px; overflow: hidden;
    box-shadow: 0 4px 14px rgba(0,0,0,0.18);
  }

  /* Front */
  .card-front {
    left: 302px; top: 126px;
    background: linear-gradient(100deg, var(--card-white) 0%, var(--white) 45%, var(--card-grey) 100%);
  }
  .front-stripe {
    position: absolute; left: 0; top: 0; width: 88px; height: 100%;
    background: var(--orange);
  }
  .brand-square {
    position: absolute; left: 52px; top: 62px; width: 64px; height: 64px;
    background: var(--orange);
    border: 4px solid var(--white);
  }
  .brand-divider {
    position: absolute; left: 147px; top: 40px; width: 2px; height: 98px;
    background: var(--orange);
  }
  .brand-block { position: absolute; left: 157px; top: 62px; }
  .brand-name {
    color: var(--orange); font-weight: 700; font-size: 19px;
    line-height: 21px; letter-spacing: 0.2px; text-transform: uppercase;
  }
  .brand-phone {
    margin-top: 4px; color: var(--orange); font-weight: 600;
    font-size: 16px; letter-spacing: 1.5px;
  }
  .contact-block {
    position: absolute; right: 42px; top: 248px; text-align: right;
    color: var(--orange);
  }
  .contact-name {
    font-weight: 700; font-size: 23px; text-transform: uppercase; letter-spacing: 0.3px;
  }
  .contact-line { font-weight: 500; font-size: 14.5px; line-height: 21px; margin-top: 2px; }

  /* Back */
  .card-back {
    left: 300px; top: 500px;
    background: linear-gradient(100deg, var(--orange-light) 0%, var(--orange) 50%, var(--orange-deep) 100%);
  }
  .back-pattern {
    position: absolute; inset: 0;
    background: linear-gradient(100deg, rgba(255,255,255,0.06), rgba(0,0,0,0.04));
  }
  .back-brand {
    position: absolute; right: 360px; top: 138px; text-align: right;
    color: var(--white); font-weight: 700; font-size: 15px; line-height: 19px;
    text-transform: uppercase;
  }
  .service-list {
    position: absolute; left: 252px; top: 124px; list-style: none;
    color: var(--white); font-weight: 500; font-size: 14.5px; line-height: 18px;
  }
  .service-list li { display: flex; align-items: center; gap: 7px; }
  .service-list li::before {
    content: ""; width: 6px; height: 6px; background: var(--white);
    transform: rotate(45deg); flex: none;
  }
</style>
</head>
<body>
<main class="canvas">
  <section class="card card-front" aria-label="Business card front">
    <div class="front-stripe"></div>
    <div class="brand-square"></div>
    <div class="brand-divider"></div>
    <div class="brand-block">
      <p class="brand-name">Holloway Paving<br>Service</p>
      <p class="brand-phone">0418259730</p>
    </div>
    <div class="contact-block">
      <p class="contact-name">Mark Holloway</p>
      <p class="contact-line">markholloway@brightmail.com.au</p>
      <p class="contact-line">ABN 62318470915</p>
    </div>
  </section>

  <section class="card card-back" aria-label="Business card back">
    <div class="back-pattern" role="img" aria-label="Faint repeating diamond brand pattern in orange tones"></div>
    <p class="back-brand">Holloway<br>Paving<br>Service</p>
    <ul class="service-list">
      <li>Excavation</li>
      <li>Exposed &amp; colour concrete</li>
      <li>House &amp; shed slabs</li>
      <li>Driveways</li>
      <li>Landing &amp; steps</li>
    </ul>
  </section>
</main>
</body>
</html>
```